Velmoria-Quillmesh Partial Redesign - Web App

Are you able to apply your creativity to an existing layout? I’m convinced that even just a few touches can make a big difference to add personality and professionalism to a website design, and I’m looking for someone able to use existing ideas and bring them to the next level while keeping inside some given constraints.
The actual job is to improve an existing design concept and to apply it creatively to a landing page, a simple home page, and an older web app (single page website).
To help you start with a clear picture of the current situation and of my requirements, I created a detailed brief with screenshots, live examples, and complete instructions. You can find it attached to this job.
My tastes are inclined towards clean and simple designs. For this project I'm not looking for dazzling novelty, but for very solid craftsmanship. Are the right man - or woman - for the job?
Updates
I wanted to thank everybody who participated in this project. I made a choice, but also other designs were interesting. Hope to work with you another time.
Target Market(s)
Our main target is social media marketers and startuppers
Look and feel
Each slider illustrates characteristics of the customer's brand and the style your logo design should communicate.

```html
<!DOCTYPE html>
<html lang="en">
<head>
<meta charset="utf-8">
<title>Velmoria – Hashtag Explorer</title>
<link href="https://fonts.googleapis.com/css2?family=PT+Sans:wght@400;700&display=swap" rel="stylesheet">
<style>
:root{
  --red:#e00d00;
  --red-dark:#b00a00;
  --ink:#2f3237;
  --dark:#3c3f45;
  --dark-2:#4a4d53;
  --grey:#c4c4c4;
  --line:#d8d8d8;
  --text:#333;
  --white:#fff;
  --cyan:#bfefff;
  --footer:#45484e;
}
*{margin:0;padding:0;box-sizing:border-box}
html,body{width:1200px;height:1134px;overflow:hidden}
body{font-family:"PT Sans",sans-serif;color:var(--text);background:var(--white);position:relative}
.abs{position:absolute}
.topline{left:0;top:0;width:1200px;height:6px;background:var(--dark)}
.header{left:0;top:6px;width:1200px;height:127px;background:linear-gradient(#f4f4f4,#e6e6e6)}
.tab{top:6px;height:27px;background:var(--dark-2);color:#fff;font-size:15px;border-radius:0 0 5px 5px;display:flex;align-items:center;justify-content:center}
.brand-mark{left:180px;top:44px;width:70px;height:70px;border-radius:50%;border:3px solid #555}
.brand{left:290px;top:40px;font-size:46px;font-weight:700;color:var(--ink);letter-spacing:-1px}
.tagline{left:304px;top:91px;font-size:15px;color:#444}
.nav{left:565px;top:65px;width:509px;height:35px;background:var(--dark-2);border-radius:6px;display:flex;align-items:center;padding:0 4px}
.nav a{flex:auto;text-align:center;color:#fff;text-decoration:none;font-size:15px;border-right:1px solid #5d6066;line-height:30px;white-space:nowrap}
.nav a:last-child{border:0}
.band{left:0;top:133px;width:1200px;height:88px;background:linear-gradient(#34373c,#45484e)}
.search{left:140px;top:165px;width:296px;height:33px;background:linear-gradient(#fff,#e7e7e7);border-radius:8px}
.search span{position:absolute;left:50px;top:9px;font-size:12px;color:#aaa;font-style:italic}
.search svg{position:absolute;left:12px;top:7px}
.btn-search{left:448px;top:164px;width:108px;height:34px;background:linear-gradient(#ff3a2a,var(--red));border-radius:6px;color:#fff;font-weight:700;font-size:17px;display:flex;align-items:center;justify-content:center}
.found{left:641px;top:170px;color:#fff;font-weight:700;font-size:17px}
.digit{top:155px;height:44px;background:#4f5258;border-radius:6px;color:#fff;font-weight:700;font-size:31px;display:flex;align-items:center;justify-content:center}
.comma{top:160px;color:#fff;font-size:30px;font-weight:700}
.tweets-count{left:872px;top:199px;color:#fff;font-size:13px}
.variants{left:129px;top:246px;width:600px;font-size:18.5px;line-height:30px;color:var(--ink)}
.variants em{font-style:normal;color:var(--red)}
.mode{top:776px;height:34px;border-radius:6px;color:#fff;font-size:17px;display:flex;align-items:center;justify-content:center}
.simple{left:405px;width:130px;background:var(--red);box-shadow:0 0 0 2px #ff6b5f inset}
.advanced{left:546px;width:161px;background:var(--dark)}
.divider{left:744px;top:252px;width:1px;height:673px;background:var(--line)}
.h-red{color:var(--red);font-weight:700;font-size:18px}
.bubble{left:905px;top:232px;width:42px;height:30px;border-radius:50%;background:var(--ink)}
.tweet{left:783px;width:292px;height:76px}
.avatar{position:absolute;left:0;top:0;width:64px;height:56px;border:3px solid #ddd;background:linear-gradient(#7a5a48,#2e2420)}
.tweet p{position:absolute;left:84px;top:-6px;width:208px;font-size:11px;line-height:14.5px;text-align:justify;color:#333}
.tweet .dot{position:absolute;left:86px;top:46px;width:20px;height:18px;border-radius:50%;background:#4fc3ee}
.tweet .time{position:absolute;left:113px;top:46px;width:90px;height:20px;border-radius:10px;background:var(--cyan);font-size:11px;display:flex;align-items:center;justify-content:center;color:#246}
.infl{left:781px;top:684px;width:285px;list-style:none}
.infl li{height:36px;border-bottom:1px dashed #ccc;font-size:14px;display:flex;align-items:center;padding-left:15px;position:relative}
.infl li::before{content:"";position:absolute;left:1px;top:14px;border-left:6px solid var(--red);border-top:4px solid transparent;border-bottom:4px solid transparent}
.infl li.top{color:var(--red)}
.followers{margin-left:18px;background:#e2e2e2;border-radius:6px;padding:2px 8px;color:#444;font-size:14px}
.footer{left:0;top:937px;width:1200px;height:197px;background:linear-gradient(var(--footer),#3b3e44);color:#fff}
.footer h3{position:absolute;top:16px;font-size:19px;font-weight:400}
.footer a{position:absolute;color:#fff;text-decoration:none;font-size:15px}
.social{position:absolute;top:56px;width:28px;height:28px;border-radius:50%;background:#6c7077}
.soc-links{position:absolute;left:421px;top:99px;font-size:13px}
.f-brand{position:absolute;left:788px;top:42px;font-size:44px;font-weight:700;color:#5a5d63}
.f-tag{position:absolute;left:802px;top:91px;font-size:15px;color:#5a5d63}
.f-mark{position:absolute;left:700px;top:40px;width:70px;height:70px;border-radius:50%;border:3px solid #5a5d63}
.legal{position:absolute;font-size:12px;color:#eee}
</style>
</head>
<body>
<div class="abs topline"></div>
<header class="abs header"></header>
<div class="abs tab" style="left:884px;width:110px">Admin Login</div>
<div class="abs tab" style="left:1006px;width:68px">Login</div>
<div class="abs brand-mark"></div>
<div class="abs brand">Velmoria</div>
<div class="abs tagline">Social Signal Brand Studio</div>
<nav class="abs nav"><a>Home</a><a>About</a><a>Blog</a><a>Summary</a><a>Timeline</a><a>Influencers</a><a>Hashtags</a></nav>

<section class="abs band"></section>
<div class="abs search"><svg width="20" height="20" viewBox="0 0 20 20"><circle cx="8" cy="8" r="6" fill="none" stroke="#999" stroke-width="2"/><line x1="12.5" y1="12.5" x2="18" y2="18" stroke="#999" stroke-width="3"/></svg><span>Search</span></div>
<div class="abs btn-search">Search</div>
<div class="abs found">HASHTAGS FOUND SO FAR:</div>
<div class="abs digit" style="left:867px;width:53px">00</div>
<div class="abs comma" style="left:923px">,</div>
<div class="abs digit" style="left:933px;width:64px">022</div>
<div class="abs comma" style="left:998px">,</div>
<div class="abs digit" style="left:1010px;width:64px">158</div>
<div class="abs tweets-count">in 567,419,411 tweets</div>

<div class="abs variants">Variants: <em>hashtag:84% Hashtag:10% HASHTAG:3% HashTag:3% hashTag:0% HASHtag:0% Popularity: 65.8</em></div>

<svg class="abs" style="left:0;top:330px" width="740" height="440" viewBox="0 330 740 440">
  <defs>
    <polygon id="pent" points="0,-1 0.951,-0.309 0.588,0.809 -0.588,0.809 -0.951,-0.309"/>
    <linearGradient id="hub" x1="0" y1="0" x2="0" y2="1"><stop offset="0" stop-color="#2c2f34"/><stop offset="1" stop-color="#55585e"/></linearGradient>
  </defs>
  <g stroke="#444" stroke-width="3">
    <line x1="425" y1="568" x2="242" y2="400"/><line x1="425" y1="568" x2="400" y2="415"/>
    <line x1="425" y1="568" x2="530" y2="490"/><line x1="425" y1="568" x2="272" y2="520"/>
    <line x1="425" y1="568" x2="190" y2="600"/><line x1="425" y1="568" x2="328" y2="640"/>
    <line x1="425" y1="568" x2="428" y2="700"/><line x1="425" y1="568" x2="545" y2="635"/>
  </g>
  <g fill="var(--grey)">
    <use href="#pent" transform="translate(242 400) rotate(-8) scale(33)"/>
    <use href="#pent" transform="translate(530 490) rotate(14) scale(48)"/>
    <use href="#pent" transform="translate(272 520) rotate(-22) scale(55)"/>
    <use href="#pent" transform="translate(190 603) rotate(-10) scale(33)"/>
    <use href="#pent" transform="translate(328 640) rotate(8) scale(40)"/>
    <use href="#pent" transform="translate(428 700) rotate(0) scale(48)"/>
    <use href="#pent" transform="translate(545 635) rotate(10) scale(65)"/>
  </g>
  <use href="#pent" fill="var(--red)" transform="translate(400 412) rotate(4) scale(66)"/>
  <use href="#pent" fill="url(#hub)" transform="translate(425 568) rotate(16) scale(56)"/>
  <g fill="#fff" font-family="PT Sans, sans-serif" font-size="17" text-anchor="middle">
    <text x="242" y="408">a</text><text x="400" y="423">you</text><text x="530" y="494">to</text>
    <text x="273" y="527">everything</text><text x="424" y="575">Hastag</text><text x="192" y="609">every</text>
    <text x="328" y="648">when</text><text x="427" y="705">que</text><text x="545" y="644">People</text>
  </g>
</svg>

<div class="abs mode simple">SIMPLE MODE</div>
<div class="abs mode advanced">ADVANCED MODE</div>
<div class="abs divider"></div>

<div class="abs h-red" style="left:779px;top:249px">FOLLOW ME ON</div>
<div class="abs bubble"></div>

<div class="abs tweet" style="top:300px"><div class="avatar" role="img" aria-label="Profile photo of the tweet author"></div><p>SunnyMira_: RT @talkyPIPA: #People #Who #Have #Too #Hashtag #Everything #On #Picstream like chill dude.</p><div class="dot"></div><div class="time">22 seconds ago</div></div>
<div class="abs tweet" style="top:382px"><div class="avatar" role="img" aria-label="Profile photo of the tweet author" style="background:linear-gradient(#e2c7b0,#8a5a3c)"></div><p>SunnyMira_: RT @talkyPIPA: #People #Who #Have #Too #Hashtag #Everything #On #Picstream like chill dude.</p><div class="dot"></div><div class="time">22 seconds ago</div></div>
<div class="abs tweet" style="top:469px"><div class="avatar" role="img" aria-label="Profile photo of the tweet author"></div><p>SunnyMira_: RT @talkyPIPA: #People #Who #Have #Too #Hashtag #Everything #On #Picstream like chill dude.</p><div class="dot"></div><div class="time">22 seconds ago</div></div>
<div class="abs tweet" style="top:551px"><div class="avatar" role="img" aria-label="Profile photo of the tweet author" style="background:linear-gradient(#e2c7b0,#8a5a3c)"></div><p>SunnyMira_: RT @talkyPIPA: #People #Who #Have #Too #Hashtag #Everything #On #Picstream like chill dude.</p><div class="dot"></div><div class="time">22 seconds ago</div></div>

<div class="abs h-red" style="left:779px;top:650px">THE TOP 6 &nbsp;INFLUENCERS FOR #TAG</div>
<ul class="abs infl">
  <li class="top">dinalorve <span class="followers">9,628,704 followers</span></li>
  <li>adrenmavik</li><li>JorrySaxon_</li><li>rolandwisp</li><li>MilaCorvin</li><li>RaneTK</li>
</ul>

<footer class="abs footer">
  <h3 style="left:150px">QUICK LINKS</h3>
  <a style="left:153px;top:56px">Home</a><a style="left:153px;top:86px">About</a><a style="left:153px;top:116px">Blog</a><a style="left:153px;top:146px">Summary</a>
  <a style="left:295px;top:56px">Timeline</a><a style="left:295px;top:86px">Influencers</a><a style="left:295px;top:116px">Hashtags</a><a style="left:295px;top:146px">Contact Us</a>
  <h3 style="left:421px">FOLLOW US ON</h3>
  <div class="social" style="left:420px"></div><div class="social" style="left:454px"></div><div class="social" style="left:488px"></div><div class="social" style="left:522px"></div>
  <div class="soc-links">chirpnet | facelink | gridplus | linkwork</div>
  <div class="f-mark"></div>
  <div class="f-brand">Velmoria</div>
  <div class="f-tag">Social Signal Brand Studio</div>
  <div class="legal" style="left:1114px;top:107px">M1</div>
  <div class="legal" style="left:851px;top:154px">Terms &amp; Conditions | Privacy Policy</div>
  <div class="legal" style="left:871px;top:175px">© 2012.www.velmoria.com</div>
</footer>
</body>
</html>
```